Supplement label and box design for Kivo/Relm Blend

we need the label and box design for our morning and nighttime supplement designed for entrepreneurs. They are energy and focus plus restorative sleep supplement stack. I have a full creative brief with video loom here: https://files.plinvora.com/doc/8kq2TzrW4mYpLx7cVn0aBdHs5eJgUf3RoiQ1tK6wZyE/view?mode=share

Target Market(s)

entreprenuers

Industry/Entity Type

Business Supplements

Requirements
Must have
• clean and sexy
Nice to have
• make sure it doesn't look like a pet supplement . . .this is for humans
Should not have
• don't use the full logo, just the text Quill Mark

```html
<!DOCTYPE html>
<html lang="en">
<head>
<meta charset="utf-8">
<title>Quill Mark – Kivo/Relm Blend labels</title>
<link rel="stylesheet" href="https://fonts.googleapis.com/css2?family=Outfit:wght@800;900&family=Oswald:wght@400;500;600&family=Poppins:wght@400;600;700&display=swap">
<style>
  :root {
    --bg: #dcdcdc;
    --paper: #ffffff;
    --ink: #2a2a2a;
    --ink-soft: #4a4a4a;
    --amber: #e9a93b;
    --amber-deep: #d8921f;
    --blue: #1f7cc4;
    --blue-deep: #1565a8;
  }
  * { box-sizing: border-box; margin: 0; padding: 0; }
  html, body { width: 1067px; height: 1200px; overflow: hidden; }
  body { background: var(--bg); position: relative; font-family: "Poppins", sans-serif; }

  .label {
    position: absolute; left: 243px; width: 580px; height: 500px;
    background: var(--paper); overflow: hidden;
    box-shadow: 0 2px 10px rgba(0,0,0,.08);
  }
  .label--am { top: 60px; --accent: var(--amber); --accent-deep: var(--amber-deep); }
  .label--pm { top: 640px; --accent: var(--blue); --accent-deep: var(--blue-deep); }

  .band-top { position: absolute; left: 0; top: 0; width: 100%; height: 32px; background: var(--accent); }
  .band-bottom { position: absolute; left: 0; bottom: 0; width: 100%; height: 40px; background: var(--accent); }
  .band-tab { position: absolute; bottom: 0; width: 210px; height: 80px; background: var(--accent); }
  .band-tab--left { left: 0; border-top-right-radius: 18px; }
  .band-tab--right { right: 0; border-top-left-radius: 18px; }

  .ribbon-text {
    position: absolute; left: 0; width: 100%;
    display: flex; justify-content: space-around;
    font-family: "Oswald", sans-serif; font-size: 8px; letter-spacing: 2px;
    color: rgba(255,255,255,.85); text-transform: uppercase; white-space: nowrap;
  }
  .band-top .ribbon-text { top: 10px; }
  .band-bottom .ribbon-text { bottom: 8px; }

  .brand-tab {
    position: absolute; left: 200px; top: 31px; width: 180px; height: 40px;
    background: var(--accent); border-radius: 0 0 20px 20px;
    display: flex; align-items: center; justify-content: center;
    font-family: "Poppins", sans-serif; font-weight: 700; font-size: 22px;
    color: var(--paper); letter-spacing: .5px; text-transform: uppercase;
  }

  .product-name {
    position: absolute; left: 0; top: 100px; width: 100%; text-align: center;
    font-family: "Outfit", sans-serif; font-weight: 900; font-size: 124px;
    line-height: 1; color: var(--ink); letter-spacing: 2px;
  }

  .benefits {
    position: absolute; left: 130px; top: 262px; width: 320px;
    display: flex; justify-content: space-between;
  }
  .benefit { width: 100px; display: flex; flex-direction: column; align-items: center; gap: 8px; }
  .benefit-icon { width: 54px; height: 54px; }
  .benefit-icon--placeholder { border-radius: 50%; background: var(--accent); opacity: .85; width: 48px; height: 48px; margin: 3px; }
  .benefit-name {
    font-family: "Oswald", sans-serif; font-weight: 500; font-size: 16px;
    color: var(--ink); text-transform: uppercase;
  }

  .directions { position: absolute; left: 48px; top: 356px; width: 160px; }
  .directions-title { font-weight: 700; font-size: 13px; line-height: 1.3; color: var(--accent-deep); }
  .directions-text { font-size: 9px; line-height: 1.3; color: var(--ink-soft); }

  .servings { position: absolute; left: 210px; top: 352px; width: 160px; text-align: center; }
  .servings-count {
    font-family: "Oswald", sans-serif; font-weight: 600; font-size: 66px;
    line-height: 1; color: var(--accent);
  }
  .servings-word {
    font-family: "Oswald", sans-serif; font-weight: 500; font-size: 22px;
    letter-spacing: 3px; color: var(--ink-soft); text-transform: uppercase; margin-top: 2px;
  }

  .pack-count, .dose {
    position: absolute; top: 430px; width: 210px; text-align: center;
    font-family: "Oswald", sans-serif; font-weight: 500; font-size: 24px;
    color: var(--paper); text-transform: uppercase;
  }
  .pack-count { left: 0; }
  .dose { right: 0; }
</style>
</head>
<body>

<section class="label label--am" aria-label="Kivo morning formula label">
  <div class="band-top"><div class="ribbon-text"><span>Dietary Supplement</span><span>Dietary Supplement</span><span>Dietary Supplement</span><span>Dietary Supplement</span></div></div>
  <div class="brand-tab">Quill Mark</div>
  <h1 class="product-name">KIVO</h1>
  <div class="benefits">
    <div class="benefit">
      <svg class="benefit-icon" viewBox="0 0 54 54" aria-hidden="true"><path d="M31 3 L13 31 H26 L21 51 L41 21 H28 Z" fill="var(--accent)"/></svg>
      <span class="benefit-name">Energy</span>
    </div>
    <div class="benefit">
      <div class="benefit-icon benefit-icon--placeholder" role="img" aria-label="Brain lightbulb icon"></div>
      <span class="benefit-name">Creativity</span>
    </div>
    <div class="benefit">
      <svg class="benefit-icon" viewBox="0 0 54 54" aria-hidden="true">
        <circle cx="27" cy="27" r="18" fill="none" stroke="var(--accent)" stroke-width="5"/>
        <circle cx="27" cy="27" r="9" fill="var(--accent)"/>
        <path d="M27 2v9M27 43v9M2 27h9M43 27h9" stroke="var(--accent)" stroke-width="4" stroke-linecap="round"/>
      </svg>
      <span class="benefit-name">Focus</span>
    </div>
  </div>
  <div class="directions">
    <p class="directions-title">Direction:</p>
    <p class="directions-text">Take 3 capsules daily, in the morning or afternoon, with or without food</p>
  </div>
  <div class="servings">
    <p class="servings-count">30</p>
    <p class="servings-word">Servings</p>
  </div>
  <div class="band-tab band-tab--left"></div>
  <div class="band-tab band-tab--right"></div>
  <div class="band-bottom"><div class="ribbon-text"><span>Dietary Supplement</span><span>Dietary Supplement</span><span>Dietary Supplement</span></div></div>
  <p class="pack-count">90 Capsules</p>
  <p class="dose">3 Per Serving</p>
</section>

<section class="label label--pm" aria-label="Relm nighttime formula label">
  <div class="band-top"><div class="ribbon-text"><span>Dietary Supplement</span><span>Dietary Supplement</span><span>Dietary Supplement</span><span>Dietary Supplement</span></div></div>
  <div class="brand-tab">Quill Mark</div>
  <h1 class="product-name">RELM</h1>
  <div class="benefits">
    <div class="benefit">
      <div class="benefit-icon benefit-icon--placeholder" role="img" aria-label="Lotus flower icon"></div>
      <span class="benefit-name">Relax</span>
    </div>
    <div class="benefit">
      <div class="benefit-icon benefit-icon--placeholder" role="img" aria-label="Reclining chair rest icon"></div>
      <span class="benefit-name">Rest</span>
    </div>
    <div class="benefit">
      <svg class="benefit-icon" viewBox="0 0 54 54" aria-hidden="true">
        <path d="M11 31 A17 17 0 0 1 40 14" fill="none" stroke="var(--accent)" stroke-width="5" stroke-linecap="round"/>
        <path d="M43 23 A17 17 0 0 1 14 40" fill="none" stroke="var(--accent)" stroke-width="5" stroke-linecap="round"/>
        <path d="M36 6 L44 15 L33 17 Z M18 48 L10 39 L21 37 Z" fill="var(--accent)"/>
        <path d="M29 15 L20 29 H27 L24 39 L34 25 H27 Z" fill="var(--accent)"/>
      </svg>
      <span class="benefit-name">Renew</span>
    </div>
  </div>
  <div class="directions">
    <p class="directions-title">Direction:</p>
    <p class="directions-text">Take 3 capsules daily, in the morning or afternoon, with or without food</p>
  </div>
  <div class="servings">
    <p class="servings-count">30</p>
    <p class="servings-word">Servings</p>
  </div>
  <div class="band-tab band-tab--left"></div>
  <div class="band-tab band-tab--right"></div>
  <div class="band-bottom"><div class="ribbon-text"><span>Dietary Supplement</span><span>Dietary Supplement</span><span>Dietary Supplement</span></div></div>
  <p class="pack-count">90 Capsules</p>
  <p class="dose">3 Per Serving</p>
</section>

</body>
</html>
```